Tall ridge firewood

It a new firewood outlet in Jindabyne nsw that will only sell top hardwood firewood (ironbark , red gum, grey gum, an box mix. I would like to see a web page the we can do order online payment for delivery. It will all so need to have photos of the firewood. I all so have logo for tall ridge firewood
Must have a modem look but easy to use I would like to see a black back ground of some sort.

Here are some other firewood web pages for ideas and firewood info
http://www.example-logpile.com.au
http://www.example-stackwood.com.au
http://www.example-splitlog.com.au
http://www.example-kendaltimber.com.au/firewood

Industry/Entity Type

Firewood

```html
<!DOCTYPE html>
<html lang="en">
<head>
<meta charset="utf-8">
<title>Tall Ridge Firewood</title>
<link href="https://fonts.googleapis.com/css2?family=Oswald:wght@500;700&family=Open+Sans:wght@400;600;700&display=swap" rel="stylesheet">
<style>
  :root {
    --nav-blue: #1c5a98;
    --nav-blue-dark: #154578;
    --heading-blue: #1f62a3;
    --accent-orange: #e97b21;
    --form-tan: #c79c66;
    --form-tan-dark: #a97d4a;
    --text-grey: #555;
    --light-grey: #f2f2f2;
    --wood-brown: #6b4527;
    --wood-light: #a8774a;
    --footer-dark: #1a1411;
    --white: #ffffff;
  }
  * { box-sizing: border-box; margin: 0; padding: 0; }
  html, body { width: 853px; height: 1200px; overflow: hidden; background: var(--white); }
  body { font-family: "Open Sans", Arial, sans-serif; color: var(--text-grey); }
  .page { position: relative; width: 853px; height: 1200px; overflow: hidden; }

  /* Top navigation */
  .site-nav {
    position: absolute; top: 0; left: 0; width: 853px; height: 34px;
    background: linear-gradient(var(--nav-blue), var(--nav-blue-dark));
    display: flex; align-items: center; justify-content: space-between; padding: 0 28px;
  }
  .brand-name { font-family: "Oswald", sans-serif; font-weight: 700; font-size: 15px; color: var(--white); text-transform: uppercase; letter-spacing: .5px; }
  .nav-links { display: flex; gap: 26px; list-style: none; }
  .nav-links li { font-family: "Oswald", sans-serif; font-weight: 500; font-size: 11px; color: var(--white); text-transform: uppercase; }

  /* Hero */
  .hero { position: absolute; top: 34px; left: 0; width: 853px; height: 236px; }
  .hero-photo { position: absolute; inset: 0; background: linear-gradient(100deg, #5a3a22 0%, #8a5c35 35%, #6b4527 60%, #4a2f1b 100%); }
  .hero-mascot { position: absolute; left: 470px; top: 8px; width: 140px; height: 210px; background: radial-gradient(ellipse at center, rgba(40,80,140,.55), rgba(40,80,140,0) 70%); }
  .hero-title { position: absolute; left: 36px; top: 34px; width: 420px; font-family: "Oswald", sans-serif; font-weight: 700; font-size: 33px; line-height: 36px; color: var(--white); text-transform: uppercase; text-shadow: 0 2px 4px rgba(0,0,0,.5); }
  .hero-call { position: absolute; left: 36px; top: 184px; display: flex; align-items: center; gap: 8px; color: var(--white); }
  .hero-call .call-label { font-size: 8px; font-weight: 700; line-height: 10px; text-transform: uppercase; }
  .hero-call .call-number { font-family: "Oswald", sans-serif; font-weight: 700; font-size: 22px; }
  .slider-arrow { position: absolute; top: 100px; width: 18px; height: 30px; }
  .slider-arrow.prev { left: 6px; } .slider-arrow.next { right: 6px; }

  /* Order panel */
  .order-panel { position: absolute; top: 222px; left: 583px; width: 240px; height: 415px; background: var(--form-tan); box-shadow: 0 2px 8px rgba(0,0,0,.3); }
  .order-title { height: 38px; background: var(--accent-orange); color: var(--white); font-family: "Oswald", sans-serif; font-weight: 700; font-size: 17px; text-transform: uppercase; display: flex; align-items: center; justify-content: center; }
  .order-intro { padding: 12px 16px 8px; font-size: 8.5px; line-height: 12px; color: var(--white); }
  .order-fields { padding: 0 16px; display: flex; flex-direction: column; gap: 9px; }
  .field { height: 24px; background: var(--white); border: 1px solid var(--form-tan-dark); font-size: 9px; color: #999; padding: 0 8px; display: flex; align-items: center; }
  .field.tall { height: 54px; align-items: flex-start; padding-top: 6px; }
  .order-next { margin: 16px auto 0; width: 96px; height: 32px; background: var(--nav-blue); color: var(--white); font-family: "Oswald", sans-serif; font-weight: 700; font-size: 15px; display: flex; align-items: center; justify-content: center; gap: 8px; border-radius: 2px; }

  /* Welcome */
  .welcome { position: absolute; top: 270px; left: 0; width: 560px; }
  .section-heading { font-family: "Oswald", sans-serif; font-weight: 700; font-size: 17px; color: var(--heading-blue); text-transform: uppercase; }
  .welcome .section-heading { position: absolute; left: 28px; top: 16px; white-space: nowrap; }
  .heading-rule { position: absolute; left: 28px; top: 42px; width: 530px; height: 2px; background: var(--heading-blue); }
  .video-thumb { position: absolute; left: 28px; top: 56px; width: 178px; height: 118px; background: radial-gradient(ellipse at 50% 70%, #f6a233 0%, #c4501b 35%, #3b1c10 80%); }
  .video-play { position: absolute; left: 70px; top: 40px; }
  .welcome-side { position: absolute; left: 218px; top: 56px; width: 340px; font-size: 9px; line-height: 13px; }
  .welcome-body { position: absolute; left: 28px; top: 186px; width: 530px; font-size: 9px; line-height: 13px; }
  .welcome-side p + p, .welcome-body p + p { margin-top: 6px; }

  /* Products */
  .products { position: absolute; top: 652px; left: 0; width: 853px; height: 215px; }
  .products .section-heading { text-align: center; font-size: 18px; }
  .product-row { position: absolute; top: 40px; left: 48px; display: flex; gap: 14px; }
  .product-card { width: 140px; text-align: center; }
  .product-photo { width: 140px; height: 100px; }
  .product-photo.mixed { background: linear-gradient(135deg, #8a5a36, #c08b5c); }
  .product-photo.unsplit { background: linear-gradient(135deg, #7a6a55, #b7a283); }
  .product-photo.kindling { background: linear-gradient(135deg, #9c6b3f, #d2a06a); }
  .product-photo.redgum { background: linear-gradient(135deg, #6e3a22, #a5603a); }
  .product-photo.mulch { background: linear-gradient(135deg, #6a4a2f, #9f7a55); }
  .product-name { margin-top: 6px; font-size: 9px; font-weight: 700; color: #333; text-transform: uppercase; }
  .product-price { font-size: 10px; font-weight: 700; color: var(--accent-orange); }
  .row-arrow { position: absolute; top: 80px; }
  .row-arrow.prev { left: 22px; } .row-arrow.next { right: 22px; }

  /* Footer */
  .site-footer { position: absolute; top: 880px; left: 0; width: 853px; height: 320px; }
  .footer-photo { position: absolute; inset: 0; background: linear-gradient(180deg, #3a2418 0%, var(--footer-dark) 55%, #0e0b09 100%); }
  .footer-col { position: absolute; top: 20px; color: #ddd; font-size: 9px; line-height: 15px; }
  .footer-col h3 { font-family: "Oswald", sans-serif; font-weight: 700; font-size: 14px; color: var(--accent-orange); text-transform: uppercase; margin-bottom: 8px; border-bottom: 1px solid #5a4636; padding-bottom: 4px; }
  .footer-nav { left: 40px; width: 250px; }
  .footer-nav .lists { display: flex; gap: 50px; }
  .footer-nav ul { list-style: none; text-transform: uppercase; }
  .footer-enquiry { left: 330px; width: 220px; }
  .footer-enquiry .phone { font-family: "Oswald", sans-serif; font-weight: 700; font-size: 17px; line-height: 22px; color: var(--white); }
  .footer-enquiry p { margin-top: 6px; }
  .footer-hours { left: 600px; width: 215px; text-transform: uppercase; }
  .footer-brand { position: absolute; left: 0; width: 853px; top: 222px; display: flex; justify-content: center; align-items: center; gap: 8px; }
  .footer-brand .brand-name { font-size: 16px; }
  .footer-brand .brand-dot { width: 14px; height: 14px; border-radius: 50%; background: var(--accent-orange); }
  .copyright { position: absolute; top: 262px; width: 853px; text-align: center; font-size: 8px; color: #aaa; }
</style>
</head>
<body>
<div class="page">

  <header class="site-nav">
    <span class="brand-name">Tall Ridge Firewood</span>
    <ul class="nav-links">
      <li>Home</li><li>Our Products</li><li>Order Online</li><li>Contact Us</li>
    </ul>
  </header>

  <section class="hero">
    <div class="hero-photo" role="img" aria-label="Stacked split hardwood firewood logs"></div>
    <div class="hero-mascot" role="img" aria-label="Lumberjack mascot holding an axe"></div>
    <h1 class="hero-title">Delivering top quality seasoned hardwood all year round</h1>
    <div class="hero-call">
      <svg width="18" height="18" viewBox="0 0 24 24" fill="#fff"><path d="M6.6 10.8a15.1 15.1 0 0 0 6.6 6.6l2.2-2.2c.3-.3.7-.4 1-.2 1.1.4 2.3.6 3.6.6.6 0 1 .4 1 1V20c0 .6-.4 1-1 1A17 17 0 0 1 3 4c0-.6.4-1 1-1h3.5c.6 0 1 .4 1 1 0 1.3.2 2.5.6 3.6.1.3 0 .7-.2 1z"/></svg>
      <span class="call-label">Call us<br>today</span>
      <span class="call-number">(02) 6100 4821</span>
    </div>
    <svg class="slider-arrow prev" viewBox="0 0 18 30"><path d="M14 3 4 15l10 12" fill="none" stroke="#fff" stroke-width="3"/></svg>
    <svg class="slider-arrow next" viewBox="0 0 18 30"><path d="M4 3l10 12L4 27" fill="none" stroke="#fff" stroke-width="3"/></svg>
  </section>

  <section class="welcome">
    <h2 class="section-heading">Welcome to our new online store</h2>
    <div class="heading-rule"></div>
    <div class="video-thumb" role="img" aria-label="Video still of a fire burning in a fireplace">
      <svg class="video-play" width="38" height="38" viewBox="0 0 38 38"><circle cx="19" cy="19" r="18" fill="#1f62a3"/><path d="M15 11v16l12-8z" fill="#fff"/></svg>
    </div>
    <div class="welcome-side">
      <p>We stock only premium seasoned hardwood, split and ready to burn. Ironbark, red gum, grey gum and box mix are cut to size, stacked dry and delivered to your door across the Snowy region.</p>
      <p>Order online in minutes, choose your load size and pick a delivery day that suits you. Secure payment is taken at checkout.</p>
    </div>
    <div class="welcome-body">
      <p>Our timber is sourced from sustainable suppliers and dried for at least twelve months, so it lights easily, burns hot and leaves very little ash. Bulk loads, kindling and mulch are also available for pickup or delivery.</p>
    </div>
  </section>

  <aside class="order-panel">
    <div class="order-title">Order Firewood</div>
    <p class="order-intro">Fill in your details below and we will confirm your order and delivery time. Payment is made securely online.</p>
    <div class="order-fields">
      <div class="field">Your Name</div>
      <div class="field">Email Address</div>
      <div class="field">Your Phone Number</div>
      <div class="field">Type of Firewood</div>
      <div class="field">Quantity</div>
      <div class="field tall">Delivery Address</div>
    </div>
    <div class="order-next">NEXT
      <svg width="12" height="12" viewBox="0 0 12 12"><path d="M3 1l6 5-6 5" fill="none" stroke="#fff" stroke-width="2.5"/></svg>
    </div>
  </aside>

  <section class="products">
    <h2 class="section-heading">New products for February</h2>
    <svg class="row-arrow prev" width="12" height="20" viewBox="0 0 12 20"><path d="M10 2 2 10l8 8" fill="none" stroke="#999" stroke-width="2.5"/></svg>
    <div class="product-row">
      <div class="product-card"><div class="product-photo mixed" role="img" aria-label="Pile of mixed hardwood"></div><div class="product-name">Mixed Hardwood</div><div class="product-price">$25.00</div></div>
      <div class="product-card"><div class="product-photo unsplit" role="img" aria-label="Unsplit round logs"></div><div class="product-name">Unsplit Wood</div><div class="product-price">$1.00 A LOG</div></div>
      <div class="product-card"><div class="product-photo kindling" role="img" aria-label="Bundle of kindling sticks"></div><div class="product-name">Bunch of Kindling</div><div class="product-price">$10.00</div></div>
      <div class="product-card"><div class="product-photo redgum" role="img" aria-label="Split red gum firewood"></div><div class="product-name">Red Gum Split</div><div class="product-price">$30.00</div></div>
      <div class="product-card"><div class="product-photo mulch" role="img" aria-label="Heap of plain wood mulch"></div><div class="product-name">Plain Wood Mulch</div><div class="product-price">$25.00</div></div>
    </div>
    <svg class="row-arrow next" width="12" height="20" viewBox="0 0 12 20"><path d="M2 2l8 8-8 8" fill="none" stroke="#999" stroke-width="2.5"/></svg>
  </section>

  <footer class="site-footer">
    <div class="footer-photo" role="img" aria-label="Dark stacked firewood background"></div>
    <div class="footer-col footer-nav">
      <h3>Navigation</h3>
      <div class="lists">
        <ul><li>Home</li><li>About us</li><li>Our products</li><li>Firewood</li><li>Contact us</li></ul>
        <ul><li>Fencing</li><li>Contact</li><li>Conditions of use</li><li>Privacy policy</li></ul>
      </div>
    </div>
    <div class="footer-col footer-enquiry">
      <h3>Enquiry Online</h3>
      <div class="phone">02 6456 2207</div>
      <div class="phone">0400 318 594</div>
      <p>Call or send us a message for bulk orders, delivery areas and seasonal pricing.</p>
    </div>
    <div class="footer-col footer-hours">
      <h3>Hours</h3>
      <p>Monday to Friday 8:00am – 5:00pm</p>
      <p>Saturday 8:00am – 3:00pm</p>
      <p>Sunday 10:00am – 2:00pm</p>
    </div>
    <div class="footer-brand"><span class="brand-dot"></span><span class="brand-name">Tall Ridge Firewood</span></div>
    <p class="copyright">Copyright © 2016 Tall Ridge Firewood. All Rights Reserved</p>
  </footer>

</div>
</body>
</html>
```